New Website Announcement

We need a flyer to announce our new website to customers and prospective clients. The website will be launching soon, but I can provide a detailed outline in PDF form with copy and imagery to serve as inspiration for this design.

I would like a postcard size document that can be mailed in an envelope (no need for postcard style mailer info on 1 side)

About my company:

Verity Lane Studio is a new breed of marketing consulting agency built for the next frontier of consumer learning. Social interaction will be at the heart of great insights going forward – in how consumers engage with brands and in how organizations socialize what they learn to gain competitive advantage.
By fusing innovative insights techniques, technology and compelling graphic design-based reporting, we ensure results get noticed and make an impact.

contact info that can also be included:

Email: marek@veritylane-studio.net

Phone: 518-732-5164

Thanks

Attention all designers submitting a design for this project. Please keep in mind a few important details about this project.

1. Remember that the main objective of this postcard is to announce my new website.

2. Please be sure to read the brief for the copy I would like on each side. You can be creative in how it is displayed, but I need this key information somewhere. All other copy on the attached files is for your background only.

3. Please do not submit overly simple designs that just take the images I provided and overlay a text box with my copy. I could easily do this myself in PowerPoint in 5 minutes.

4. Remember that the design should be edgy and modern but needs to be professional and speak to a business audience.

Please submit any questions. Thank you for your submissions. 

Marek

Target Market(s)

senior level marketing and research clients at large companies and agencies

Industry/Entity Type

Marketing

Requirements
Must have
• Main message:

Need an engaging way to tell customers and prospective clients that we have a new website and that they should come visit us online to learn more about out services, check out case studies and read about our exciting partnerships.

COPY TO USE - UPDATED

Side 1:
(logo)
Introducing Verity Lane Studio

Let’s talk about taking research out of the dark ages.

Visit our newly launched website to learn how and get in touch.

www.veritylane-studio.net

Side 2
Logo
followed by tagline:
Consumer insights that get noticed.
A leading-edge marketing partnership that really works.

Additional text to use on Side 2:
How we can help...

Think of us as your go-to resource for identifying and incorporating the most innovative and exciting techniques into your research programs. We carefully curate and develop close partnerships with the best of the best - from online qualitative research and mobile ethnography to social media listening and fresh takes on concept testing, we can guide the way.

Plus, we believe that socializing consumer learning is just as critical as gathering it.By taking insights deliverables to the next level – through infographics, videos, magazines,interactive profiles and so much more – we are getting stakeholders excited to engage with research and inspired to take action because of it.
It’s a new way to look at insights from a new type of partner. And, it’s a new way to get the most from your research dollars.
Nice to have
• could incorporate our website main image of the lamp on white brick background which is attached, but not 100% mandatory.
Should not have
• - should not be too playful or young, but needs to be modern and design focused

- should not be cluttered or overly 'salesy'

- needs to be upscale and elegant / compelling and aligned with the look and feel of the website imagery (see attached)

```html
<!DOCTYPE html>
<html lang="en">
<head>
<meta charset="utf-8">
<title>Verity Lane Studio – New Website Postcard</title>
<link rel="stylesheet" href="https://fonts.googleapis.com/css2?family=Open+Sans:wght@400;600&family=PT+Sans+Narrow:wght@700&family=Roboto+Slab:wght@300;400&display=swap">
<style>
  :root {
    --page: #ffffff;
    --card: #ffffff;
    --brand-blue: #1f6fc1;
    --ribbon-blue: #2a7fd0;
    --ink: #1a1a1a;
    --body-ink: #2b2b2b;
    --banner-black: #0b0b0b;
    --white: #ffffff;
    --wall-light: #f1f1f0;
    --wall-mid: #cfcfcd;
    --wall-dark: #8e8e8c;
  }
  * { box-sizing: border-box; margin: 0; padding: 0; }
  html, body { width: 1200px; height: 453px; overflow: hidden; background: var(--page); }
  .canvas { position: relative; width: 1200px; height: 453px; }

  .card {
    position: absolute; top: 30px; width: 548px; height: 392px;
    background: var(--card);
    box-shadow: 2px 4px 8px rgba(0,0,0,0.28);
    overflow: hidden;
  }
  .card--front { left: 30px; }
  .card--back { left: 622px; }

  /* Front */
  .hero-photo {
    position: absolute; left: 41px; top: 40px; width: 462px; height: 313px;
    background:
      radial-gradient(ellipse 160px 140px at 190px 110px, rgba(255,255,255,0.95), rgba(255,255,255,0) 70%),
      linear-gradient(180deg, var(--wall-light) 0%, var(--wall-mid) 60%, var(--wall-dark) 72%, #b9b9b7 80%, #d6d6d4 100%);
  }
  .front-name {
    position: absolute; left: 290px; top: 58px; width: 210px;
    font-family: "PT Sans Narrow", sans-serif; font-weight: 700;
    font-size: 40px; line-height: 40px; color: var(--brand-blue);
    text-align: center;
  }
  .ribbon {
    position: absolute; left: 0; top: 0; width: 548px; height: 392px; pointer-events: none;
  }
  .ribbon__band {
    position: absolute; left: -5px; top: 103px; width: 270px; height: 32px;
    transform: rotate(-45deg);
    background: var(--ribbon-blue);
    box-shadow: 1px 3px 5px rgba(0,0,0,0.35);
    font-family: "Open Sans", sans-serif; font-size: 15px; color: var(--white);
    display: flex; align-items: center; justify-content: center; letter-spacing: 0.2px;
  }

  .banner {
    position: absolute; background: linear-gradient(180deg, #2a2a2a 0%, var(--banner-black) 45%, #000 100%);
    box-shadow: 1px 3px 4px rgba(0,0,0,0.4);
    color: var(--white);
    font-family: "PT Sans Narrow", sans-serif; font-weight: 700;
  }
  .banner--front {
    left: 41px; top: 295px; width: 462px; height: 42px;
    padding: 3px 0 0 34px; font-size: 15.5px; line-height: 18px;
  }
  .banner--back {
    left: 68px; top: 117px; width: 445px; height: 26px;
    padding: 0 0 0 20px; font-size: 19px; line-height: 26px;
  }
  .dot {
    position: absolute; border-radius: 50%;
    background: radial-gradient(circle at 40% 35%, #5fa8ee 0%, #2272c8 55%, #14529a 100%);
    border: 4px solid var(--white);
    box-shadow: 0 2px 5px rgba(0,0,0,0.45);
  }
  .dot--front { left: 29px; top: 293px; width: 44px; height: 44px; }
  .dot--back { left: 38px; top: 112px; width: 40px; height: 40px; }

  /* Back */
  .back-name {
    position: absolute; left: 40px; top: 44px; width: 130px;
    font-family: "PT Sans Narrow", sans-serif; font-weight: 700;
    font-size: 25px; line-height: 26px; color: var(--brand-blue);
  }
  .tagline {
    position: absolute; left: 186px; top: 43px;
    font-family: "PT Sans Narrow", sans-serif; font-weight: 700;
    font-size: 16px; line-height: 19px; color: var(--brand-blue);
  }
  .body-copy {
    position: absolute; left: 88px; top: 152px; width: 432px;
    font-family: "Open Sans", sans-serif; font-size: 9.3px; line-height: 16.3px;
    color: var(--body-ink);
  }
  .contact {
    position: absolute; left: 88px; top: 325px;
    font-family: "Roboto Slab", serif; font-weight: 400;
    font-size: 10.5px; line-height: 15px; color: var(--brand-blue);
  }
</style>
</head>
<body>
<main class="canvas">
  <section class="card card--front" aria-label="Postcard front">
    <div class="hero-photo" role="img" aria-label="Photo of a black arc floor lamp lighting a whitewashed brick wall above a concrete floor"></div>
    <div class="front-name">Verity Lane Studio</div>
    <div class="banner banner--front">
      Let’s talk about taking research out of the dark ages.<br>
      Visit our newly launched website to learn how and get in touch.
    </div>
    <div class="dot dot--front"></div>
    <div class="ribbon"><div class="ribbon__band">www.veritylane-studio.net</div></div>
  </section>

  <section class="card card--back" aria-label="Postcard back">
    <div class="back-name">Verity Lane Studio</div>
    <p class="tagline">Consumer insights that get noticed.<br>A leading-edge marketing partnership that really works</p>
    <h2 class="banner banner--back">How we can help...</h2>
    <div class="dot dot--back"></div>
    <div class="body-copy">
      <p>Think of us as your go-to resource for identifying and incorporating the most innovative and exciting techniques into your research programs. We carefully curate and develop close partnerships with the best of the best - from online qualitative research and mobile ethnogra&shy;phy to social media listening and fresh takes on concept testing, we can guide the way.</p>
      <p>Plus, we believe that socializing consumer learning is just as critical as gathering it. By taking insights deliverables to the next level – through infographics, videos, magazines, interactive profiles and so much more – we are getting stakeholders excited to engage with research and inspired to take action because of it.</p>
      <p>It’s a new way to look at insights from a new type of partner. And, it’s a new way to get the most from your research dollars.</p>
    </div>
    <div class="contact">
      Email: marek@veritylane-studio.net<br>
      Phone: 518-732-5164
    </div>
  </section>
</main>
</body>
</html>
```